Up to the Challenge - PPT Template with Splash Slide

We are looking for a PPT template that has 4 slides.
1. Splash slide (Creative, fun, no content, a visual representation of the theme)
2. Section header slide
3. Content Slide
4. Content Slide, another design option
The theme is 'UP to the Challenge'. The design should reflect this theme.
The colors should be in Purple (#864B99), Blue (#0A80C2), and Green (#52B054).

```html
<!DOCTYPE html>
<html lang="en">
<head>
<meta charset="utf-8">
<title>Up to the Challenge – Slide Template</title>
<link rel="stylesheet" href="https://fonts.googleapis.com/css2?family=Montserrat:wght@400;500;600;700&family=Nunito:wght@600;700&display=swap">
<style>
:root{
  --purple:#864B99;
  --blue:#0A80C2;
  --green:#52B054;
  --ink:#222222;
  --body:#444444;
  --canvas:#F0F0F0;
  --white:#FFFFFF;
}
*{box-sizing:border-box;margin:0;padding:0}
html,body{width:1017px;height:1200px;overflow:hidden;background:var(--canvas)}
body{position:relative;font-family:"Montserrat",Arial,sans-serif;color:var(--body)}
.slide{position:absolute;width:482px;height:270px;background:var(--white);overflow:hidden;box-shadow:0 1px 3px rgba(0,0,0,.18)}
.col-left{left:16px}.col-right{left:514px}
.row-1{top:15px}.row-2{top:312px}.row-3{top:608px}.row-4{top:905px}
.fill{position:absolute;inset:0;width:100%;height:100%}
.accent-bars{position:absolute;display:flex;gap:3px}
.accent-bars span{display:block;width:22px;height:2px;border-radius:1px}
.accent-bars span:nth-child(1){background:var(--purple)}
.accent-bars span:nth-child(2){background:var(--blue)}
.accent-bars span:nth-child(3){background:var(--green)}
.title{position:absolute;font-family:"Nunito",Arial,sans-serif;font-weight:600;font-size:16.5px;letter-spacing:.3px;color:var(--ink);white-space:nowrap}
.date{position:absolute;left:12px;top:256px;font-family:"Nunito",Arial,sans-serif;font-size:6.4px;font-weight:700;color:var(--ink)}
.page-no{position:absolute;left:452px;top:246px;width:16px;height:16px;border-radius:50%;background:var(--green);color:var(--white);font-size:6px;font-weight:700;display:flex;align-items:center;justify-content:center}
.text{position:absolute;font-size:8.6px;line-height:12.3px;color:var(--body)}
.text p+p{margin-top:11px}
.lead{color:var(--green);font-weight:500}
.hl{color:var(--purple);font-weight:500}
.item{position:absolute}
.item h3{font-size:7.8px;font-weight:700;color:var(--ink);letter-spacing:.2px}
.item p{margin-top:6px;font-size:7px;line-height:10.6px;color:var(--body)}
.icon{position:absolute}
.photo-frame{position:absolute;border-radius:8px;overflow:hidden}
</style>
</head>
<body>

<!-- 1 Splash -->
<section class="slide col-left row-1">
  <svg class="fill" viewBox="0 0 482 270" role="img" aria-label="Photo of a climber hanging from a rock overhang against a sunset sky">
    <defs>
      <linearGradient id="sky" x1="0" y1="0" x2="1" y2="1">
        <stop offset="0" stop-color="#86B6CF"/><stop offset=".55" stop-color="#C9D6D6"/><stop offset=".8" stop-color="#E9CFA2"/><stop offset="1" stop-color="#6E5440"/>
      </linearGradient>
    </defs>
    <rect width="482" height="270" fill="url(#sky)"/>
  </svg>
  <svg class="fill" viewBox="0 0 482 270" aria-hidden="true">
    <path d="M0 118C12 200 110 262 279 270H0Z" fill="var(--green)"/>
    <path d="M0 175C16 228 90 262 200 270H0Z" fill="var(--purple)"/>
    <path d="M0 215C14 246 50 264 110 270H0Z" fill="var(--blue)"/>
  </svg>
</section>

<!-- 2 Splash, strip variant -->
<section class="slide col-right row-1">
  <svg class="fill" viewBox="0 0 482 270" role="img" aria-label="Hiker with a backpack looking over a mountain valley, shown in four colour-tinted strips">
    <defs>
      <linearGradient id="stripP" x1="0" y1="0" x2="0" y2="1"><stop offset="0" stop-color="#B07CC0"/><stop offset="1" stop-color="#6A2F84"/></linearGradient>
      <linearGradient id="stripG" x1="0" y1="0" x2="0" y2="1"><stop offset="0" stop-color="#7FCB7F"/><stop offset="1" stop-color="#2F9A3A"/></linearGradient>
      <linearGradient id="stripN" x1="0" y1="0" x2="0" y2="1"><stop offset="0" stop-color="#D6D9D6"/><stop offset=".5" stop-color="#7D7767"/><stop offset="1" stop-color="#4F5038"/></linearGradient>
      <linearGradient id="stripB" x1="0" y1="0" x2="0" y2="1"><stop offset="0" stop-color="#1A9BD6"/><stop offset="1" stop-color="#0A5EAA"/></linearGradient>
    </defs>
    <rect x="0" width="121" height="270" fill="url(#stripP)"/>
    <rect x="121" width="120" height="270" fill="url(#stripG)"/>
    <rect x="241" width="120" height="270" fill="url(#stripN)"/>
    <rect x="361" width="121" height="270" fill="url(#stripB)"/>
  </svg>
</section>

<!-- 3 Section header, circle -->
<section class="slide col-left row-2">
  <svg class="fill" viewBox="0 0 482 270" aria-hidden="true">
    <circle cx="114" cy="92" r="160" fill="var(--purple)"/>
  </svg>
  <svg class="fill" viewBox="0 0 482 270" role="img" aria-label="Photo of a team gathered around a laptop in a bright office">
    <defs>
      <linearGradient id="office" x1="0" y1="0" x2="1" y2="1"><stop offset="0" stop-color="#3A3A38"/><stop offset=".5" stop-color="#B79A7A"/><stop offset="1" stop-color="#D8C6AE"/></linearGradient>
      <clipPath id="officeClip"><circle cx="108" cy="92" r="156"/></clipPath>
    </defs>
    <rect width="482" height="270" fill="url(#office)" clip-path="url(#officeClip)"/>
  </svg>
  <div class="accent-bars" style="left:300px;top:119px"><span></span><span></span><span></span></div>
  <h2 class="title" style="left:300px;top:129px">INTRODUCTION</h2>
  <div class="date">June 2024</div>
  <div class="page-no">02</div>
</section>

<!-- 4 Section header, wave -->
<section class="slide col-right row-2">
  <svg class="fill" viewBox="0 0 482 270" role="img" aria-label="Aerial photo of a rowing crew on deep blue water">
    <defs>
      <linearGradient id="water" x1="0" y1="0" x2="1" y2="1"><stop offset="0" stop-color="#1D4F6E"/><stop offset="1" stop-color="#2A6F95"/></linearGradient>
    </defs>
    <path d="M0 0H482V150C430 210 340 240 270 220 170 190 80 160 0 180Z" fill="url(#water)"/>
  </svg>
  <svg class="fill" viewBox="0 0 482 270" aria-hidden="true">
    <path d="M0 178C80 160 170 188 270 218 340 240 430 212 482 150V158C430 222 340 252 270 232 170 200 80 166 0 180Z" fill="var(--purple)"/>
    <path d="M270 232C340 252 430 222 482 158V166C430 232 340 262 270 242 200 222 130 196 70 174 140 186 200 212 270 232Z" fill="var(--blue)"/>
    <path d="M270 242C340 262 430 232 482 166V176C430 242 340 272 270 252 200 232 130 200 70 174 130 196 200 222 270 242Z" fill="var(--green)"/>
  </svg>
  <div class="accent-bars" style="left:13px;top:195px"><span></span><span></span><span></span></div>
  <h2 class="title" style="left:13px;top:204px">INTRODUCTION</h2>
  <div class="date">June 2024</div>
  <div class="page-no">02</div>
</section>

<!-- 5 About us, two columns -->
<section class="slide col-left row-3">
  <div class="accent-bars" style="left:204px;top:22px"><span></span><span></span><span></span></div>
  <h2 class="title" style="left:0;width:482px;text-align:center;top:32px">ABOUT US</h2>
  <div class="text" style="left:12px;top:77px;width:224px">
    <p><span class="lead">Sed ut perspiciatis unde omnis iste natus error sit vo luptatem accusantium doloremque laudantium,</span> totam rem aperiam, eaque ipsa quae ab illo inventore veritatis et quasi architecto beatae vitae dicta sunt ex plicabo. Nemo enim ipsam voluptatem quia voluptas sit aspernatur aut odit aut fugit, sed quia consequun tur magni dolores eos qui ratione voluptatem sequi nesciunt.</p>
    <p>Natus error sit vo luptatem accusantium doloremque laudantium, totam rem aperiam, eaque ipsa quae ab illo inventore veritatis et quasi architect.</p>
  </div>
  <div class="text" style="left:252px;top:77px;width:224px">
    <p>Sed ut perspiciatis unde omnis iste natus error sit vo luptatem accusantium doloremque laudantium, totam rem aperiam, eaque ipsa quae ab illo inventore veritatis et quasi architecto beatae vitae</p>
    <p>Sed ut perspiciatis unde omnis <span class="hl">iste natus error sit vo luptatem accusantium doloremque</span> laudantium, totam rem aperiam, eaque ipsa quae</p>
    <p>Natus error sit vo luptatem accusantium doloremque laudantium, totam rem aperiam, eaque ipsa quae ab illo inventore veritatis et quasi architecto beatae vitae dicta sunt ex plicabo.</p>
  </div>
  <div class="date">June 2024</div>
  <div class="page-no">03</div>
</section>

<!-- 6 About us, icon list -->
<section class="slide col-right row-3">
  <div class="accent-bars" style="left:12px;top:22px"><span></span><span></span><span></span></div>
  <h2 class="title" style="left:12px;top:32px">ABOUT US</h2>
  <div class="text" style="left:12px;top:77px;width:224px">
    <p><span class="lead">Sed ut perspiciatis unde omnis iste natus error sit vo luptatem accusantium doloremque laudantium,</span> totam rem aperiam, eaque ipsa quae ab illo inventore veritatis et quasi architecto beatae vitae dicta sunt ex plicabo. Nemo enim ipsam voluptatem quia voluptas sit aspernatur aut odit aut fugit, sed quia consequun tur magni dolores eos qui ratione voluptatem sequi nesciunt.</p>
    <p>Natus error sit vo luptatem accusantium doloremque laudantium, totam rem aperiam, eaque ipsa quae ab illo inventore veritatis et quasi architect.</p>
  </div>
  <svg class="icon" style="left:244px;top:71px" width="30" height="30" viewBox="0 0 30 30" fill="none" stroke="var(--purple)" stroke-width="1.2" aria-hidden="true">
    <circle cx="14" cy="16" r="11"/><circle cx="14" cy="16" r="7"/><circle cx="14" cy="16" r="3"/>
    <path d="M14 16L25 5M21 5h4v4"/>
  </svg>
  <svg class="icon" style="left:246px;top:126px" width="26" height="30" viewBox="0 0 26 30" fill="none" stroke="var(--blue)" stroke-width="1.2" aria-hidden="true">
    <path d="M13 1l1.6 3.3 3.6.5-2.6 2.5.6 3.6L13 9.2 9.8 10.9l.6-3.6-2.6-2.5 3.6-.5z"/>
    <circle cx="13" cy="17" r="3.5"/><path d="M6 29v-2a7 7 0 0 1 14 0v2z"/>
  </svg>
  <svg class="icon" style="left:244px;top:182px" width="30" height="30" viewBox="0 0 30 30" fill="none" stroke="var(--green)" stroke-width="1.2" aria-hidden="true">
    <path d="M2 24v-6h3v6zM8 24V12h3v12zM14 24V8h3v4M20 12V3h3v7"/>
    <circle cx="19" cy="19" r="5"/><path d="M22.5 22.5L27 27"/><path d="M19 16v6M17.5 17.5h2.5a1 1 0 0 1 0 2h-1.5a1 1 0 0 0 0 2h2"/>
  </svg>
  <div class="item" style="left:288px;top:78px;width:185px"><h3>LOREM IPSUM</h3><p>Architecto beatae vitae dicta sunt ex plicabo. Nemo enim ipsam voluptatem qarchitecto beatae vitae.</p></div>
  <div class="item" style="left:288px;top:132px;width:185px"><h3>LOREM IPSUM</h3><p>Architecto beatae vitae dicta sunt ex plicabo. Nemo enim ipsam voluptatem qarchitecto beatae vitae.</p></div>
  <div class="item" style="left:288px;top:188px;width:185px"><h3>LOREM IPSUM</h3><p>Architecto beatae vitae dicta sunt ex plicabo. Nemo enim ipsam voluptatem qarchitecto beatae vitae.</p></div>
  <div class="date">June 2024</div>
  <div class="page-no">03</div>
</section>

<!-- 7 What we do, photo -->
<section class="slide col-left row-4">
  <div class="accent-bars" style="left:204px;top:22px"><span></span><span></span><span></span></div>
  <h2 class="title" style="left:0;width:482px;text-align:center;top:32px">WHAT WE DO</h2>
  <div class="text" style="left:12px;top:77px;width:224px">
    <p><span class="lead">Sed ut perspiciatis unde omnis iste natus error sit vo luptatem accusantium doloremque laudantium,</span> totam rem aperiam, eaque ipsa quae ab illo inventore veritatis et quasi architecto beatae vitae dicta sunt ex plicabo. Nemo enim ipsam voluptatem quia voluptas sit aspernatur aut odit aut fugit, sed quia consequun tur magni dolores eos qui ratione voluptatem sequi nesciunt.</p>
    <p>Natus error sit vo luptatem accusantium doloremque laudantium, totam rem aperiam, eaque ipsa quae ab illo inventore veritatis et quasi architect.</p>
  </div>
  <div class="photo-frame" style="left:260px;top:76px;width:209px;height:144px">
    <svg class="fill" viewBox="0 0 209 144" preserveAspectRatio="none" role="img" aria-label="Photo of a climber scaling a rock face above a fjord at sunset">
      <defs>
        <linearGradient id="fjord" x1="0" y1="0" x2="1" y2="1"><stop offset="0" stop-color="#7E95A2"/><stop offset=".4" stop-color="#D9A36C"/><stop offset=".7" stop-color="#5A4E44"/><stop offset="1" stop-color="#2F2D2B"/></linearGradient>
      </defs>
      <rect width="209" height="144" fill="url(#fjord)"/>
    </svg>
  </div>
  <div class="date">June 2024</div>
  <div class="page-no">04</div>
</section>

<!-- 8 What we do, timeline -->
<section class="slide col-right row-4">
  <svg class="fill" viewBox="0 0 482 270" aria-hidden="true">
    <path d="M213 38A185 185 0 0 1 213 226" fill="none" stroke="#CFCFCF" stroke-width=".8"/>
    <circle cx="228" cy="62" r="18" fill="var(--purple)"/>
    <circle cx="251" cy="132" r="18" fill="var(--blue)"/>
    <circle cx="228" cy="202" r="18" fill="var(--green)"/>
    <g fill="none" stroke="var(--white)" stroke-width="1.5" stroke-linecap="round">
      <circle cx="226" cy="60" r="5"/><path d="M229.5 63.5L234 68"/>
      <path d="M251 139l-6-6a3.5 3.5 0 0 1 6-4 3.5 3.5 0 0 1 6 4z"/>
      <circle cx="228" cy="202" r="3"/>
      <path d="M228 194v2.5M228 207.5v2.5M220 202h2.5M233.5 202h2.5M222.3 196.3l1.8 1.8M231.9 205.9l1.8 1.8M222.3 207.7l1.8-1.8M231.9 198.1l1.8-1.8"/>
    </g>
  </svg>
  <div class="accent-bars" style="left:12px;top:86px"><span></span><span></span><span></span></div>
  <h2 class="title" style="left:12px;top:96px">WHAT WE DO</h2>
  <div class="text" style="left:12px;top:128px;width:180px">
    <p><span class="lead">Q</span>ae ab illo inventore veritatis et quasi arch itecto beatae vitae dicta sunt ex plicabo. Nemo enim ipsam voluptatem quia volup tas sit aspernatur aut odit aut fugit, sed quia consequun tur magni dolores eos.</p>
  </div>
  <div class="item" style="left:259px;top:51px;width:200px"><h3>LOREM IPSUM</h3><p>Architecto beatae vitae dicta sunt ex plicabo. Nemo enim ipsam voluptatem qarchitecto beatae vitae.</p></div>
  <div class="item" style="left:281px;top:121px;width:195px"><h3>LOREM IPSUM</h3><p>Architecto beatae vitae dicta sunt ex plicabo. Nemo enim ipsam voluptatem qarchitecto beatae vitae.</p></div>
  <div class="item" style="left:259px;top:191px;width:200px"><h3>LOREM IPSUM</h3><p>Architecto beatae vitae dicta sunt ex plicabo. Nemo enim ipsam voluptatem qarchitecto beatae vitae.</p></div>
  <div class="date">June 2024</div>
  <div class="page-no">04</div>
</section>

</body>
</html>
```